Client Meeting and installation Email Follow up

I would like a follow-up email template created.
Currently, we do a lot of new construction builds and meet with clients about 6-3 months before they take possession of their new house. I want a follow-up email template to be sent after the homeowner takes possession of their house that enquires if the clients are happy about their new lighting, the service they received, and their customer service representative with Brightwell Lamps and Breezes. I have attached a few files of what our current marketing looks like.
Target Market(s)
Home Owners We have already met with
Industry/Entity Type
Residential lighting
Font styles to use
Other font styles liked:
- Alta Light, Playfair Display, Montserrat
Colors
Designer to choose colors to be used in the design.
Look and feel
Each slider illustrates characteristics of the customer's brand and the style your logo design should communicate.

```html
<!DOCTYPE html>
<html lang="en">
<head>
<meta charset="utf-8">
<title>Brightwell Lamps and Breezes – Residential Lighting Follow-up</title>
<link rel="stylesheet" href="https://fonts.googleapis.com/css2?family=Josefin+Sans:wght@300;400;600&family=Marcellus&display=swap">
<style>
:root{
  --paper:#ffffff;
  --bronze:#a2845f;
  --taupe:#aa9376;
  --ink:#2b2622;
  --white:#ffffff;
  --line-soft:rgba(255,255,255,.8);
  --rule:#c9c3bc;
}
*{margin:0;padding:0;box-sizing:border-box}
html,body{width:1200px;height:3536px;overflow:hidden;background:var(--paper)}
body{position:relative;font-family:'Josefin Sans',sans-serif;color:var(--ink)}
.abs{position:absolute}
.photo{position:absolute}
.brand{font-family:'Josefin Sans',sans-serif;font-weight:400;color:var(--ink);text-transform:uppercase;line-height:1.1;white-space:nowrap}
.brand-top{left:75px;top:24px;font-size:34px;z-index:3}
.hero-title{left:75px;top:212px;font-family:'Marcellus',serif;font-weight:400;font-size:63px;line-height:86px;color:var(--bronze);white-space:nowrap;z-index:5}
.card-tilt{position:absolute;background:#fff;padding:10px;box-shadow:0 4px 14px rgba(0,0,0,.18);z-index:1}
.card-tilt div{width:100%;height:100%}
.intro-box{left:389px;top:822px;width:736px;height:393px;border:1.5px solid var(--bronze)}
.intro-copy{left:622px;top:860px;width:450px}
.intro-copy h2{font-weight:400;font-size:34px;color:var(--bronze);letter-spacing:.5px;margin-bottom:22px;white-space:nowrap}
.intro-copy p{font-weight:300;font-size:26px;line-height:42px}
.feedback{left:0;top:1354px;width:1200px;height:1701px;background:var(--taupe)}
.feedback-title{left:0;top:1440px;width:1200px;text-align:center;color:var(--white);font-weight:400;font-size:35px;line-height:54px;letter-spacing:.5px}
.topic-box{position:absolute;border:1.5px solid var(--line-soft)}
.topic{position:absolute;color:var(--white);width:555px}
.topic h3{font-weight:400;font-size:27px;letter-spacing:.5px;margin-bottom:20px}
.topic p{font-weight:300;font-size:27px;line-height:45px}
.topic b{font-weight:600}
.brand-foot{left:0;width:1200px;top:3175px;text-align:center;font-size:40px}
.contact{position:absolute;top:3340px;display:flex;gap:14px;align-items:flex-start}
.contact svg{margin-top:30px}
.contact .label{color:var(--bronze);font-weight:600;font-size:27px;line-height:36px}
.contact .value{font-weight:300;font-size:26px;line-height:40px;white-space:nowrap}
.rule{left:75px;top:3440px;width:1050px;height:2px;background:var(--rule)}
.copyright{left:0;top:3462px;width:1200px;text-align:center;font-weight:300;font-size:26px}
</style>
</head>
<body>

<div class="abs brand brand-top">Brightwell Lamps<br>and Breezes</div>

<div class="photo" role="img" aria-label="Bedroom with grey bedding and a round rug" style="left:810px;top:0;width:390px;height:646px;background:linear-gradient(180deg,#e6e6e4,#8f9498 70%,#d8d6d2);clip-path:polygon(30% 0,100% 0,100% 100%,0 100%,8% 40%)"></div>
<div class="photo" role="img" aria-label="Modern glass globe chandelier" style="left:960px;top:0;width:150px;height:170px;background:linear-gradient(180deg,#cfcfcf,#f2f2f2)"></div>

<div class="card-tilt" style="left:480px;top:150px;width:180px;height:200px;transform:rotate(12deg)"><div role="img" aria-label="Kitchen with pendant lights and bar stools" style="background:linear-gradient(180deg,#eeeeec,#c9a27a)"></div></div>
<div class="card-tilt" style="left:680px;top:60px;width:190px;height:215px;transform:rotate(-10deg)"><div role="img" aria-label="Bathroom vanity with wall lights" style="background:linear-gradient(180deg,#d9d5cf,#7a5a3c)"></div></div>
<div class="card-tilt" style="left:535px;top:400px;width:280px;height:245px;transform:rotate(8deg)"><div role="img" aria-label="Dining area with pendant lamps" style="background:linear-gradient(180deg,#e8e6e3,#a88f78)"></div></div>

<h1 class="abs hero-title">RESIDENTIAL<br>LIGHTING AND<br>INSTALLATION</h1>

<div class="photo" role="img" aria-label="Black pendant lamp" style="left:760px;top:646px;width:190px;height:155px;background:linear-gradient(180deg,#ffffff 0 30%,#2b2b2b 60%,#f4e3b5)"></div>

<div class="photo" role="img" aria-label="Dining room with a dark chandelier and round mirror" style="left:75px;top:771px;width:481px;height:583px;background:linear-gradient(180deg,#e7e7e5,#a9a9a4 60%,#6d6a66)"></div>
<div class="abs intro-box"></div>
<div class="abs intro-copy">
  <h2>WE ARE HERE FOR YOU</h2>
  <p>Brightwell Lamps and Breezes, we’re dedicated to ensuring that every detail of your lighting installation meets your expectations. We’d love to hear about your experience with our services and the installation process.</p>
</div>

<div class="abs feedback"></div>
<div class="photo" role="img" aria-label="Black pendant lamp" style="left:10px;top:1354px;width:200px;height:160px;background:linear-gradient(180deg,var(--taupe) 0 30%,#2b2b2b 60%,#f4e3b5)"></div>
<h2 class="abs feedback-title">HERE ARE A FEW THINGS WE’D APPRECIATE<br>YOUR FEEDBACK ON:</h2>

<div class="topic-box" style="left:74px;top:1621px;width:618px;height:345px"></div>
<div class="photo" role="img" aria-label="Dining table with tulips and a chandelier" style="left:692px;top:1602px;width:436px;height:387px;background:linear-gradient(180deg,#7d8a96,#5a6b7b 60%,#b07a45)"></div>
<div class="topic" style="left:110px;top:1706px">
  <h3>LIGHTING DESIGN</h3>
  <p><b>Consultation and Planning:</b> Assessing the lighting needs of a space and creating a plan that addresses both aesthetics and functionality.</p>
</div>

<div class="photo" role="img" aria-label="White kitchen with pendant lights" style="left:74px;top:2070px;width:435px;height:384px;background:linear-gradient(180deg,#e9eaeb,#cfd1d3 60%,#f4f4f4)"></div>
<div class="topic-box" style="left:509px;top:2086px;width:603px;height:345px"></div>
<div class="topic" style="left:542px;top:2172px">
  <h3>INSTALLATION</h3>
  <p><b>Fixture Installation:</b> Installing various lighting fixtures such as chandeliers, recessed lights, pendant lights, and sconces.</p>
</div>

<div class="topic-box" style="left:76px;top:2551px;width:616px;height:345px"></div>
<div class="photo" role="img" aria-label="Kitchen island with pendant lights and wooden stools" style="left:692px;top:2532px;width:436px;height:386px;background:linear-gradient(180deg,#f1f1ef,#dcd6cf 55%,#c49a6c)"></div>
<div class="topic" style="left:102px;top:2637px">
  <h3>MAINTENANCE AND REPAIRS</h3>
  <p>Routine Maintenance: Checking and maintaining lighting systems to ensure they function properly, including cleaning fixtures and replacing bulbs.</p>
</div>

<div class="abs brand brand-foot">Brightwell Lamps<br>and Breezes</div>

<div class="contact" style="left:75px">
  <svg width="28" height="28" viewBox="0 0 24 24"><path fill="var(--bronze)" d="M6.6 10.8a15 15 0 0 0 6.6 6.6l2.2-2.2a1 1 0 0 1 1-.25 11.4 11.4 0 0 0 3.6.6 1 1 0 0 1 1 1V20a1 1 0 0 1-1 1A17 17 0 0 1 3 4a1 1 0 0 1 1-1h3.5a1 1 0 0 1 1 1c0 1.25.2 2.45.6 3.6a1 1 0 0 1-.25 1z"/></svg>
  <div><div class="label">Phone No:</div><div class="value">+1(555)010 0199</div></div>
</div>
<div class="contact" style="left:365px">
  <svg width="34" height="26" viewBox="0 0 24 18"><path fill="var(--bronze)" d="M0 2l12 8 12-8V0H0zM0 4.5V18h24V4.5l-12 8z"/></svg>
  <div><div class="label">Email:</div><div class="value">hello@brightwelllamps.net</div></div>
</div>
<div class="contact" style="left:808px">
  <svg width="24" height="34" viewBox="0 0 24 34"><path fill="var(--bronze)" d="M12 0A12 12 0 0 0 0 12c0 9 12 22 12 22s12-13 12-22A12 12 0 0 0 12 0zm0 17a5 5 0 1 1 0-10 5 5 0 0 1 0 10z"/></svg>
  <div><div class="label">Location:</div><div class="value">Brightwell Lamps, USA</div></div>
</div>

<div class="abs rule"></div>
<p class="abs copyright">Copyright © 2024 Brightwell Lamps| All Rights Reserved</p>

</body>
</html>
```